Silver Meadow LLC business card

I help with the Marketing and Sales of various Natural, Organic, Eco Friendly and Healthy Main Stream products to Retail Corporate accounts as well as Independents and Distributors.I also highlight Private label items to these same Retail Corporate accounts.Cherish the Moments, Enjoy Life!

Speciality & Health Sales and Marketing

Target Market(s)

Men and Women

Industry/Entity Type

Business

Contact Information for Business Card

Silver Meadow, LLC
Janet Louise Verhagen
438 West Finch Lane
Ste 4-237
Phoenix, AZ 85047
602-555-0147
jverhagen@plumvale.net

Requirements
Must have
• Nice, femine font
Something in the background or on a side with a softness
Nice to have
• Cherish the Moments, Enjoy Life
Should not have
• Hardness

```html
<!DOCTYPE html>
<html lang="en">
<head>
<meta charset="utf-8">
<title>Silver Meadow LLC – Business Card</title>
<link rel="stylesheet" href="https://fonts.googleapis.com/css2?family=Parisienne&family=Roboto+Condensed:wght@400;500&display=swap">
<style>
  :root {
    --page-bg: #ececec;
    --card-white: #ffffff;
    --dome-green: #a6c91c;
    --ink: #1c1c1c;
    --icon-fill: #1c1c1c;
    --icon-glyph: #a6c91c;
  }
  html, body {
    margin: 0;
    width: 1200px;
    height: 963px;
    overflow: hidden;
    background: var(--page-bg);
  }
  .business-card {
    position: absolute;
    left: 180px;
    top: 241px;
    width: 840px;
    height: 480px;
    background: var(--card-white);
    overflow: hidden;
    box-shadow: 0 2px 10px rgba(0,0,0,0.12);
  }
  .card-art {
    position: absolute;
    inset: 0;
  }
  .brand-name {
    position: absolute;
    left: 140px;
    top: 150px;
    margin: 0;
    font-family: "Parisienne", cursive;
    font-weight: 400;
    font-size: 56px;
    line-height: 1;
    color: var(--ink);
  }
  .name-rule {
    position: absolute;
    left: 120px;
    top: 222px;
    width: 470px;
    border-top: 2px dotted var(--ink);
  }
  .contact-list {
    position: absolute;
    left: 150px;
    top: 236px;
    margin: 0;
    padding: 0;
    list-style: none;
    font-family: "Roboto Condensed", sans-serif;
    font-weight: 500;
    font-size: 22px;
    line-height: 27px;
    color: var(--ink);
  }
  .contact-item {
    display: flex;
    align-items: flex-start;
    gap: 12px;
    margin-bottom: 16px;
  }
  .contact-icon {
    flex: none;
    width: 22px;
    height: 22px;
    margin-top: 3px;
  }
  .contact-icon circle { fill: var(--icon-fill); }
  .contact-icon .glyph { fill: var(--icon-glyph); }
  .contact-icon .glyph-line { fill: none; stroke: var(--icon-glyph); stroke-width: 1.4; }
</style>
</head>
<body>
  <article class="business-card">
    <svg class="card-art" width="840" height="480" viewBox="0 0 840 480">
      <defs>
        <linearGradient id="spectrumFan" x1="0" y1="0.5" x2="1" y2="0.75">
          <stop offset="0" stop-color="#a8326f"/>
          <stop offset="0.12" stop-color="#d9457f"/>
          <stop offset="0.3" stop-color="#2f6db5"/>
          <stop offset="0.45" stop-color="#1ea3c7"/>
          <stop offset="0.62" stop-color="#a6c91c"/>
          <stop offset="0.8" stop-color="#f2cc1e"/>
          <stop offset="1" stop-color="#ee6a12"/>
        </linearGradient>
        <radialGradient id="fanSoftening" cx="0.36" cy="1" r="0.8">
          <stop offset="0.55" stop-color="#ffffff" stop-opacity="0.85"/>
          <stop offset="0.8" stop-color="#ffffff" stop-opacity="0"/>
        </radialGradient>
      </defs>
      <g class="spectrum-fan" role="img" aria-label="Soft rainbow fan of fine white grid lines sweeping from magenta through blue and green to orange">
        <rect width="840" height="480" fill="url(#spectrumFan)"/>
        <rect width="840" height="480" fill="url(#fanSoftening)"/>
      </g>
      <ellipse class="dome-rim" cx="300" cy="500" rx="412" ry="382" fill="#ffffff"/>
      <ellipse class="dome" cx="300" cy="500" rx="400" ry="370" fill="var(--dome-green)"/>
    </svg>

    <h1 class="brand-name">Silver Meadow</h1>
    <div class="name-rule"></div>

    <ul class="contact-list">
      <li class="contact-item">
        <svg class="contact-icon" viewBox="0 0 22 22" aria-hidden="true">
          <circle cx="11" cy="11" r="11"/>
          <path class="glyph" d="M11 4.5a4 4 0 0 0-4 4c0 3 4 8 4 8s4-5 4-8a4 4 0 0 0-4-4zm0 5.6a1.6 1.6 0 1 1 0-3.2 1.6 1.6 0 0 1 0 3.2z"/>
        </svg>
        <span>LLC Janet Louise Verhagen 438<br>West Finch Lane Ste 4-237 Phoenix<br>AZ 85047</span>
      </li>
      <li class="contact-item">
        <svg class="contact-icon" viewBox="0 0 22 22" aria-hidden="true">
          <circle cx="11" cy="11" r="11"/>
          <rect class="glyph" x="7.5" y="5" width="7" height="12" rx="1.2"/>
          <rect x="8.6" y="6.5" width="4.8" height="7.5" fill="#1c1c1c"/>
        </svg>
        <span>602-555-0147</span>
      </li>
      <li class="contact-item">
        <svg class="contact-icon" viewBox="0 0 22 22" aria-hidden="true">
          <circle cx="11" cy="11" r="11"/>
          <rect class="glyph-line" x="5.5" y="7" width="11" height="8"/>
          <path class="glyph-line" d="M5.5 7l5.5 4.5L16.5 7"/>
        </svg>
        <span>jverhagen@plumvale.net</span>
      </li>
    </ul>
  </article>
</body>
</html>
```